** Wanted ** Wordpress web design for scaffolding rental and construction company

We need a website design and must be functional to show a basic overview of what our company offers as a service. We have a domain name and a logo but we need web design. This web site should have another scaffolding rental page for construction and renovation as well as a quote section where customers can enter their personal information and also upload photos. The site% 26quot; www.brindlework.com% 26quot; should be intuitive, clear and classy ... The logo must be found on the site in several ways.

Target Market(s)

Professional and no professional

Coding

Coded - Design and coding required

Number of Pages Required

3 page

Font styles to use
Serif
Sans Serif
Decorative
Script

Requirements
Must have
• Our logo
Nice to have
• Slogan:% 26quot; The height% 26 # 224; port% 26 # 233; e hand% 26quot;

```html
<!DOCTYPE html>
<html lang="en">
<head>
<meta charset="utf-8">
<title>Brindlework — Scaffolding Rental and Construction</title>
<link href="https://fonts.googleapis.com/css2?family=Roboto:wght@300;400;500;700&family=Open+Sans:wght@400;600&display=swap" rel="stylesheet">
<style>
:root{
  --blue:#1a88e0;
  --blue-dark:#0f6fc0;
  --ink:#1b1b1b;
  --text:#555;
  --grey-bg:#efefef;
  --dark:#2a2f36;
  --black:#0a0a0a;
  --white:#fff;
}
*{box-sizing:border-box;margin:0;padding:0}
html,body{width:1200px;height:4164px;overflow:hidden}
body{position:relative;font-family:"Open Sans",sans-serif;color:var(--text);background:var(--white)}
.abs{position:absolute}
.heading{font-family:"Roboto",sans-serif;font-weight:500;color:var(--ink);text-transform:uppercase}
.heading .accent{color:var(--blue)}
.center{text-align:center}

/* hero */
.hero{position:absolute;left:0;top:0;width:1200px;height:708px;background:linear-gradient(180deg,#4d5259 0%,#6f7378 35%,#5b5a4e 70%,#3a3a32 100%)}
.hero-nav a{position:absolute;font-family:"Roboto",sans-serif;font-weight:500;font-size:14px;color:var(--white);text-decoration:none;text-transform:uppercase}
.nav-active{border-bottom:3px solid var(--blue);padding-bottom:6px}
.brand{position:absolute;left:493px;top:76px;width:214px;height:42px;display:flex;align-items:center;justify-content:center;gap:10px;font-family:"Roboto",sans-serif;font-weight:700;font-size:20px;letter-spacing:2px;color:var(--white)}
.brand-mark{width:14px;height:14px;background:var(--blue)}
.phone{position:absolute;left:912px;top:36px;font-family:"Roboto",sans-serif;font-size:18px;color:var(--white);display:flex;gap:6px;align-items:center}
.hero-kicker{position:absolute;left:0;width:1200px;top:276px;font-family:"Roboto",sans-serif;font-weight:300;font-size:33px;color:var(--white);text-align:center}
.hero-title{position:absolute;left:0;width:1200px;top:316px;font-family:"Roboto",sans-serif;font-weight:700;font-size:48px;line-height:55px;color:var(--white);text-align:center}
.btn-solid{position:absolute;background:var(--blue);color:var(--white);font-family:"Roboto",sans-serif;font-weight:500;font-size:15px;display:flex;align-items:center;justify-content:center}
.btn-outline{position:absolute;border:2px solid currentColor;font-family:"Roboto",sans-serif;font-weight:500;font-size:15px;display:flex;align-items:center;justify-content:center;text-transform:uppercase}
.slide-arrow{position:absolute;width:56px;height:56px;border-radius:50%;background:rgba(255,255,255,.25);display:flex;align-items:center;justify-content:center}

/* about */
.about-visual{position:absolute;left:150px;top:740px;width:390px;height:395px;background:linear-gradient(180deg,#e9e9e9,#c9c9c9 60%,#f6f6f6)}
.about-copy{position:absolute;left:577px;top:880px;width:500px;font-size:13px;line-height:23px;color:var(--text)}
.about-copy p+p{margin-top:22px}

/* services */
.service{position:absolute;top:1215px;height:445px;color:var(--white);text-align:center}
.service-rental{left:0;width:596px;background:linear-gradient(135deg,#3c3f44,#5f6166 50%,#3d3e40)}
.service-build{left:596px;width:604px;background:linear-gradient(135deg,#1a88e0,#3b9ae6 50%,#1576c8)}
.service h3{position:absolute;left:0;right:0;top:170px;font-family:"Roboto",sans-serif;font-weight:500;font-size:30px}
.service p{position:absolute;left:0;right:0;top:215px;font-size:15px;line-height:23px}

/* why */
.why{position:absolute;left:0;top:1660px;width:1200px;height:608px;background:var(--grey-bg)}
.feature h4{font-family:"Roboto",sans-serif;font-weight:500;font-size:17px;color:var(--ink);margin-bottom:8px}
.feature p{font-size:12px;line-height:19.5px;color:var(--text)}
.feature{position:absolute;width:250px}
.feature.left{text-align:right}

/* projects */
.project-main{position:absolute;left:338px;top:2395px;width:522px;height:400px;background:linear-gradient(180deg,#8a8d90,#6a6a66 60%,#4a4a48)}
.project-caption{position:absolute;left:338px;width:522px;text-align:center;color:var(--white)}

/* customers */
.client{position:absolute;top:3022px;font-family:"Roboto",sans-serif;font-weight:700;font-size:28px;color:#6a6a6a;display:flex;align-items:center;gap:8px}
.client .dot{width:14px;height:14px;background:#6a6a6a}

/* news */
.news-img{position:absolute;top:3330px;width:305px;height:162px}
.news-card{position:absolute;top:3490px;width:270px;height:120px;background:var(--white);box-shadow:0 4px 10px rgba(0,0,0,.15);text-align:center;padding-top:16px}
.news-card h5{font-family:"Roboto",sans-serif;font-weight:500;font-size:15px;color:var(--ink);margin-bottom:6px}
.news-card p{font-size:11px;line-height:15px;color:#777;padding:0 30px}
.plus{position:absolute;top:3598px;width:30px;height:30px;background:var(--black);transform:rotate(45deg);display:flex;align-items:center;justify-content:center}
.plus span{transform:rotate(-45deg);color:var(--white);font-size:20px;line-height:1;font-family:"Roboto",sans-serif}

/* footer */
.footer-col{position:absolute;top:3838px;color:#ddd}
.footer-col h6{font-family:"Roboto",sans-serif;font-weight:500;font-size:17px;color:var(--white);margin-bottom:20px}
.footer-col li{list-style:none;font-size:14px;line-height:27px}
.footer-col .row{display:flex;align-items:center;gap:10px;font-size:14px;line-height:35px}
.legal{position:absolute;left:0;top:4102px;width:1200px;height:62px;background:var(--dark);color:#aaa;font-size:12px;display:flex;align-items:center;justify-content:center}
</style>
</head>
<body>

<!-- Hero -->
<header class="hero" role="img" aria-label="Workers in safety vests looking up at a steel scaffolding structure"></header>
<nav class="hero-nav">
  <a href="#" class="nav-active" style="left:107px;top:92px">About Us</a>
  <a href="#" style="left:215px;top:92px">Scaffolding</a>
  <a href="#" style="left:350px;top:92px">Projects</a>
  <a href="#" style="left:757px;top:87px">Services</a>
  <a href="#" style="left:862px;top:87px">Our News</a>
  <a href="#" style="left:973px;top:87px">Contact Us</a>
</nav>
<div class="brand"><span class="brand-mark"></span>BRINDLEWORK</div>
<div class="phone">
  <svg width="16" height="16" viewBox="0 0 24 24"><path fill="#1a88e0" d="M6.6 10.8a15.1 15.1 0 0 0 6.6 6.6l2.2-2.2c.3-.3.7-.4 1-.2 1.1.4 2.3.6 3.6.6.6 0 1 .4 1 1V20c0 .6-.4 1-1 1C10.6 21 3 13.4 3 4c0-.6.4-1 1-1h3.5c.6 0 1 .4 1 1 0 1.3.2 2.5.6 3.6.1.3 0 .7-.2 1z"/></svg>
  (555) 014 2270
</div>
<div class="hero-kicker">WELCOME TO BRINDLEWORK</div>
<h1 class="hero-title">SCAFFOLDING RENTAL AND<br>CONSTRUCTION</h1>
<a class="btn-solid" style="left:506px;top:443px;width:188px;height:47px">LEARN MORE</a>
<div class="slide-arrow" style="left:60px;top:352px"><svg width="26" height="20" viewBox="0 0 26 20"><path d="M25 10H2M10 2 2 10l8 8" stroke="#fff" stroke-width="2" fill="none"/></svg></div>
<div class="slide-arrow" style="left:1072px;top:352px"><svg width="26" height="20" viewBox="0 0 26 20"><path d="M1 10h23M16 2l8 8-8 8" stroke="#fff" stroke-width="2" fill="none"/></svg></div>

<!-- About -->
<section>
  <div class="about-visual" role="img" aria-label="Two-bay aluminium scaffold tower with wooden platforms"></div>
  <h2 class="heading abs" style="left:573px;top:815px;font-size:33px"><span class="accent">About</span> Brindlework</h2>
  <div class="about-copy">
    <p>Praesent elementum elit at tellus Curabitur metus ipsum luctus eu male-suada ut tincidunt sed diam vdisse risus nibh ultricies eu</p>
    <p>Maecenas aliquet velit vel turpis Mauris neque metus malesuada nec ultricies sit amet porttitor mattis enim In massa libero interdum nec interdum vel blandit sed nulla In ullamcorper est eget tempor cursus neque mi consect-etuer mi a ultricies massa est sed nisl</p>
  </div>
  <a class="btn-outline" style="left:582px;top:1074px;width:175px;height:47px;color:var(--blue)">Learn More</a>
</section>

<!-- Services -->
<section>
  <div class="service service-rental" role="img" aria-label="Scaffolding on a building site">
    <svg class="abs" style="left:265px;top:82px" width="68" height="68" viewBox="0 0 68 68" fill="none" stroke="#fff" stroke-width="2.5"><rect x="4" y="4" width="60" height="8"/><path d="M8 12v52M60 12v52M8 12l52 52M60 12 8 64M2 64h64"/></svg>
    <h3>SCAFFOLDING RENTAL</h3>
    <p>Praesent elementum elit at tellus Curabitur metus ipsum<br>luctus eu malesuada ut tincidunt sed diam</p>
    <a class="btn-outline" style="left:205px;top:288px;width:175px;height:47px;color:var(--white)">Learn More</a>
  </div>
  <div class="service service-build" role="img" aria-label="Scaffolding under a blue tint">
    <svg class="abs" style="left:265px;top:82px" width="72" height="68" viewBox="0 0 72 68" fill="none" stroke="#fff" stroke-width="2.5"><path d="M4 12v52h64V24M4 12h20l-4-8H4zM30 50l30-34 6 6-30 34-8 2zM14 56h12M14 46l10-8 10 8"/></svg>
    <h3>CONSTRUCTION SERVICES</h3>
    <p>Praesent elementum elit at tellus Curabitur metus ipsum<br>luctus eu malesuada ut tincidunt sed diam</p>
    <a class="btn-outline" style="left:226px;top:288px;width:175px;height:47px;color:var(--white)">Learn More</a>
  </div>
  <svg class="abs" style="left:0;top:1580px" width="1200" height="82" viewBox="0 0 1200 82"><polygon points="420,82 600,8 780,82" fill="#efefef"/></svg>
</section>

<!-- Why we are -->
<section class="why">
  <h2 class="heading abs center" style="left:0;width:1200px;top:53px;font-size:30px"><span class="accent">Why we</span> are</h2>
  <svg class="abs" style="left:0;top:0" width="1200" height="608" viewBox="0 0 1200 608">
    <g fill="none" stroke="#bbb" stroke-width="1"><path d="M503 200h40l30 30M697 200h-40l-30 30M503 450h40l30-30M697 450h-40l-30-30"/></g>
    <g fill="#1a88e0"><circle cx="503" cy="200" r="5"/><circle cx="697" cy="200" r="5"/><circle cx="503" cy="450" r="5"/><circle cx="697" cy="450" r="5"/></g>
    <polygon points="600,195 730,325 600,455 470,325" fill="#6b6b6b"/>
    <g fill="#fff" stroke="#1a88e0" stroke-width="2">
      <rect x="417" y="178" width="50" height="50" transform="rotate(45 442 203)"/>
      <rect x="738" y="178" width="50" height="50" transform="rotate(45 763 203)"/>
      <rect x="417" y="428" width="50" height="50" transform="rotate(45 442 453)"/>
      <rect x="738" y="428" width="50" height="50" transform="rotate(45 763 453)"/>
    </g>
    <g fill="none" stroke="#222" stroke-width="2">
      <path d="M426 195v16M458 195v16M426 200h32M426 206h32M432 195v16M452 195v16"/>
      <path d="M750 212h26M753 212v-4a10 10 0 0 1 20 0v4M759 200v-6h8v6"/>
      <path d="M430 441l24 24M454 441l-24 24M428 443l4-4M456 463l-4 4"/>
      <rect x="751" y="445" width="24" height="18" rx="2"/><path d="M755 445l8-7 8 7"/>
    </g>
    <text x="763" y="458" font-size="7" font-family="Roboto" text-anchor="middle" fill="#222">SALE</text>
  </svg>
  <div class="abs" style="left:470px;top:195px;width:260px;height:260px" role="img" aria-label="Scaffolding photo in a diamond frame"></div>
  <div class="feature left" style="left:133px;top:155px"><h4>Scaffolding Systems</h4><p>Praesent sit amet est In dictum dolor eu dictum porttitor enim felis viverra mi eget luctus massa purus quis</p></div>
  <div class="feature" style="left:826px;top:155px"><h4>Safety systems</h4><p>Praesent sit amet est In dictum dolor eu dictum porttitor enim felis viverra mi eget luctus massa purus quis</p></div>
  <div class="feature left" style="left:133px;top:405px"><h4>Reliable Services</h4><p>Praesent sit amet est In dictum dolor eu dictum porttitor enim felis viverra mi eget luctus massa purus quis</p></div>
  <div class="feature" style="left:826px;top:405px"><h4>For Sale</h4><p>Praesent sit amet est In dictum dolor eu dictum porttitor enim felis viverra mi eget luctus massa purus quis</p></div>
</section>

<!-- Projects -->
<section>
  <h2 class="heading abs center" style="left:0;width:1200px;top:2318px;font-size:30px"><span class="accent">Our</span> Projects</h2>
  <svg class="abs" style="left:0;top:2395px" width="1200" height="400" viewBox="0 0 1200 400" role="img" aria-label="Side project photos of scaffolding in greyscale">
    <polygon points="0,40 315,0 315,400 0,360" fill="#cfcfcf"/>
    <polygon points="882,0 1200,40 1200,360 882,400" fill="#d3d3d3"/>
    <polygon points="0,40 315,0 315,400 0,360" fill="#fff" opacity=".3"/>
    <polygon points="882,0 1200,40 1200,360 882,400" fill="#fff" opacity=".3"/>
  </svg>
  <div class="project-main" role="img" aria-label="Building facade wrapped in scaffolding"></div>
  <div class="project-caption heading" style="top:2690px;font-size:20px;color:var(--white)">Project Title Here</div>
  <div class="project-caption" style="top:2722px;font-size:13px;line-height:19px">Praesent elementum elit at tellus Curabitur metus ipsum<br>luctus eu malesuada ut tincidunt</div>
  <svg class="abs" style="left:243px;top:2566px" width="58" height="58" viewBox="0 0 58 58"><circle cx="29" cy="29" r="29" fill="#1a88e0"/><path d="M41 29H17M25 21l-8 8 8 8" stroke="#fff" stroke-width="2.5" fill="none"/></svg>
  <svg class="abs" style="left:904px;top:2566px" width="58" height="58" viewBox="0 0 58 58"><circle cx="29" cy="29" r="29" fill="#1a88e0"/><path d="M17 29h24M33 21l8 8-8 8" stroke="#fff" stroke-width="2.5" fill="none"/></svg>
</section>

<!-- Customers -->
<section>
  <h2 class="heading abs center" style="left:0;width:1220px;top:2913px;font-size:26px"><span class="accent">Our</span> Customers</h2>
  <svg class="abs" style="left:68px;top:3016px" width="48" height="48" viewBox="0 0 48 48"><circle cx="24" cy="24" r="24" fill="#999"/><path d="M34 24H14M21 17l-7 7 7 7" stroke="#fff" stroke-width="2" fill="none"/></svg>
  <svg class="abs" style="left:1086px;top:3016px" width="48" height="48" viewBox="0 0 48 48"><circle cx="24" cy="24" r="24" fill="#999"/><path d="M14 24h20M27 17l7 7-7 7" stroke="#fff" stroke-width="2" fill="none"/></svg>
  <div class="client" style="left:152px"><span class="dot"></span>Norvale</div>
  <div class="client" style="left:362px;font-size:22px">Tessly Works</div>
  <div class="client" style="left:552px">KARVEN</div>
  <div class="client" style="left:748px">Orlet Guild</div>
  <div class="client" style="left:936px">Quillo</div>
</section>

<!-- News -->
<section>
  <svg class="abs" style="left:0;top:3180px" width="1200" height="922" viewBox="0 0 1200 922">
    <rect x="0" y="0" width="1200" height="922" fill="#0a0a0a"/>
    <polygon points="0,0 1200,0 1200,472 650,472 600,588 550,472 0,472" fill="#1a88e0"/>
    <polygon points="0,472 550,472 600,588 650,472 1200,472 1200,470 0,470" fill="#1a88e0"/>
    <polygon points="0,472 600,490 1200,472" fill="#1a88e0"/>
  </svg>
  <h2 class="heading abs center" style="left:0;width:1200px;top:3245px;font-size:28px;color:var(--white)">Latest News</h2>

  <div class="news-img" style="left:128px;background:linear-gradient(180deg,#6aa0d8,#c59a5a)" role="img" aria-label="Orange scaffolding against a blue sky"></div>
  <div class="news-img" style="left:460px;background:linear-gradient(180deg,#a9c9e6,#8a9a6a)" role="img" aria-label="Worker in high-visibility gear on scaffolding"></div>
  <div class="news-img" style="left:790px;background:linear-gradient(180deg,#b8c4cf,#6a6f75)" role="img" aria-label="Roof framing surrounded by scaffolding"></div>

  <div class="news-card" style="left:146px"><h5>FUSCE TELLUS SED</h5><p>Curabitur vel dolor ultrices ipsum dictum tristique Praesent vitae lacus Ut velit enim</p></div>
  <div class="news-card" style="left:478px"><h5>PRAESENT SIT AMET EST</h5><p>Curabitur vel dolor ultrices ipsum dictum tristique Praesent vitae lacus Ut velit enim</p></div>
  <div class="news-card" style="left:810px"><h5>NUNC TEMPUS FELIS VITAE</h5><p>Curabitur vel dolor ultrices ipsum dictum tristique Praesent vitae lacus Ut velit enim</p></div>
  <div class="plus" style="left:266px"><span>+</span></div>
  <div class="plus" style="left:597px"><span>+</span></div>
  <div class="plus" style="left:929px"><span>+</span></div>
  <svg class="abs" style="left:572px;top:3722px" width="56" height="56" viewBox="0 0 56 56"><circle cx="28" cy="28" r="26" fill="#fff"/></svg>
</section>

<!-- Footer -->
<footer>
  <div class="footer-col" style="left:155px"><h6>COMPANY</h6><ul><li>Home</li><li>About Us</li><li>Scaffolding</li><li>Services</li><li>Projects</li></ul></div>
  <div class="footer-col" style="left:337px"><h6>RESOURCES</h6><ul><li>Blogs</li><li>News</li><li>Clients</li><li>Support</li><li>Contact Us</li></ul></div>
  <div class="footer-col" style="left:570px"><h6>CONTACT US</h6>
    <div class="row"><svg width="16" height="18" viewBox="0 0 16 18"><path d="M8 0a6 6 0 0 0-6 6c0 5 6 12 6 12s6-7 6-12a6 6 0 0 0-6-6zm0 8.5A2.5 2.5 0 1 1 8 3.5a2.5 2.5 0 0 1 0 5z" fill="#fff"/></svg>48 Harlow Lane, Suite 3, Fenwick TX</div>
    <div class="row"><svg width="16" height="16" viewBox="0 0 24 24"><path fill="#fff" d="M6.6 10.8a15.1 15.1 0 0 0 6.6 6.6l2.2-2.2c.3-.3.7-.4 1-.2 1.1.4 2.3.6 3.6.6.6 0 1 .4 1 1V20c0 .6-.4 1-1 1C10.6 21 3 13.4 3 4c0-.6.4-1 1-1h3.5c.6 0 1 .4 1 1 0 1.3.2 2.5.6 3.6.1.3 0 .7-.2 1z"/></svg>(555) 017 3384</div>
    <div class="row"><svg width="18" height="14" viewBox="0 0 18 14"><rect x="1" y="1" width="16" height="12" fill="none" stroke="#fff" stroke-width="1.6"/><path d="M1 1l8 6 8-6" stroke="#fff" stroke-width="1.6" fill="none"/></svg>hello@brindlework.com</div>
  </div>
  <div class="footer-col" style="left:914px"><h6>FOLLOW US</h6>
    <div class="row"><svg width="14" height="14"><circle cx="7" cy="7" r="5" fill="#fff"/></svg>Network</div>
    <div class="row"><svg width="14" height="14"><circle cx="7" cy="7" r="5" fill="#fff"/></svg>Community</div>
    <div class="row"><svg width="14" height="14"><circle cx="7" cy="7" r="5" fill="#fff"/></svg>Updates</div>
  </div>
  <div class="legal">© 2020 Brindlework | All Rights Reserved | Disclaimer</div>
</footer>

</body>
</html>
```